Brightway Haus Inc. Business Card Design

Brightway Haus Inc. is in search of a great clean design for our business cards!

Looking to incorporate our full logo and watermark on side one (however, I am open to having the text and watermark separated within the design.)

On side two, I am looking to have contact information (Name, Position, Phone #, Email, Website (www.thebrightwayhaus.ca). Can have the logo and/or watermark as part of the design if applicable.

Please add tagline "Where Shine Counts" on either side 1 or 2. This tagline can be in a sans serif, serif or cursive font as long as it compliments overall design. Capitalization can be title or sentence case depending on how it fits within the design.

Get creative!! Looking for a clean, crisp, premium design! Looking for a glossy card finish with spot UV features when printed. Cards will also be printed with rounded corners. Standard dimensions (3.5 x 2).

Target Market(s)

B2B - primary clients are business owners or property management corporations. (residential jobs are few and far between)

Industry/Entity Type

Business

Contact Information for Business Card

- clean, crisp design
- double sided
- spot UV accents and glossy finish upon printing
- standard business card size (3.5 x 2) with rounded corners
- please see project description for requirements per side

Font styles to use
Sans Serif

Requirements
Must have
• - adequate bleeds with print ready files
• - cohesive design elements between side 1 & 2
• - spot UV elements (can be on both sides or just one, use your discretion)
• - colour pallet should match the logo file provided
• - incorporate tagline "where shine counts" (this tagline can be in a serif or sans serif font as long as it is complimentary to the overall design.
Nice to have
• - Premium elements with a clean design
Should not have
• - Please omit cartoon or whimsical like designs, think premium.
• - Colours should not stray from the pallet of the provided logo.

```html
<!DOCTYPE html>
<html lang="en">
<head>
<meta charset="utf-8">
<title>Brightway Haus Inc. Business Cards</title>
<link href="https://fonts.googleapis.com/css2?family=Roboto:ital,wght@0,400;0,500;0,700;1,400&display=swap" rel="stylesheet">
<style>
  :root {
    --backdrop: #2b2b2b;
    --paper: #f3f3f3;
    --navy: #1b2550;
    --teal: #12b5b8;
    --white: #ffffff;
    --grey: #a9abaf;
  }
  * { box-sizing: border-box; margin: 0; padding: 0; }
  html, body { width: 1200px; height: 960px; overflow: hidden; }
  body {
    background: var(--backdrop);
    font-family: "Roboto", Arial, sans-serif;
    position: relative;
  }
  .card {
    position: absolute;
    width: 600px;
    height: 342px;
    border-radius: 22px;
    overflow: hidden;
    box-shadow: 0 6px 14px rgba(0,0,0,.45);
  }
  .card--front { left: 314px; top: 114px; background: var(--paper); }
  .card--back { left: 311px; top: 473px; background: var(--navy); }

  .brand {
    position: absolute;
    left: 0; right: 0;
    display: flex;
    align-items: center;
    justify-content: center;
    gap: 12px;
    font-weight: 700;
    font-size: 40px;
    letter-spacing: -0.5px;
    white-space: nowrap;
  }
  .brand__square { width: 34px; height: 34px; flex: none; }
  .card--front .brand { top: 70px; color: var(--navy); }
  .card--front .brand__square { background: var(--teal); }
  .card--back .brand { top: 148px; color: var(--white); }
  .card--back .brand__square { background: var(--teal); }

  .info-band {
    position: absolute;
    left: 0; right: 0;
    top: 193px;
    height: 125px;
    display: flex;
  }
  .identity {
    width: 298px;
    background: var(--teal);
    color: var(--white);
    text-align: right;
    padding: 24px 32px 0 0;
    font-size: 14.5px;
    line-height: 19px;
  }
  .identity__name { font-size: 20px; font-weight: 700; line-height: 22px; }
  .identity__role { font-weight: 500; }
  .band-gap { width: 4px; background: var(--paper); }
  .contacts {
    flex: 1;
    background: var(--navy);
    color: var(--white);
    list-style: none;
    padding: 24px 0 0 34px;
    font-size: 14.5px;
    line-height: 19.5px;
  }
  .contacts li { display: flex; align-items: center; gap: 8px; }
  .contacts svg { width: 13px; height: 13px; fill: var(--teal); flex: none; }

  .tagline {
    position: absolute;
    top: 274px;
    left: 100px; right: 100px;
    display: flex;
    align-items: center;
    gap: 6px;
    color: var(--white);
    font-style: italic;
    font-size: 19px;
    white-space: nowrap;
  }
  .tagline__rule { flex: 1; height: 1px; }
  .tagline__rule--left { background: linear-gradient(to right, transparent, rgba(255,255,255,.8)); }
  .tagline__rule--right { background: linear-gradient(to left, transparent, rgba(255,255,255,.8)); }
  .tagline__accent { color: var(--teal); }
</style>
</head>
<body>
  <section class="card card--front" aria-label="Card front">
    <div class="brand"><span class="brand__square"></span>Brightway Haus Inc.</div>
    <div class="info-band">
      <div class="identity">
        <p class="identity__name">MARCUS HALE</p>
        <p class="identity__role">CEO/FOUNDER</p>
        <p>4120 Larkspur Road</p>
        <p>Juneau, Alaska 21908</p>
      </div>
      <div class="band-gap"></div>
      <ul class="contacts">
        <li><svg viewBox="0 0 24 24"><path d="M6.6 10.8a15.1 15.1 0 0 0 6.6 6.6l2.2-2.2c.3-.3.7-.4 1-.2 1.1.4 2.3.6 3.6.6.6 0 1 .4 1 1V20c0 .6-.4 1-1 1A17 17 0 0 1 3 4c0-.6.4-1 1-1h3.5c.6 0 1 .4 1 1 0 1.3.2 2.5.6 3.6.1.3 0 .7-.2 1z"/></svg>907 215 4486</li>
        <li><svg viewBox="0 0 24 24"><path d="M7 1h10a2 2 0 0 1 2 2v18a2 2 0 0 1-2 2H7a2 2 0 0 1-2-2V3a2 2 0 0 1 2-2zm0 3v14h10V4z"/></svg>907 331 7720</li>
        <li><svg viewBox="0 0 24 24"><path d="M6 2h12v5H6zM3 8h18a2 2 0 0 1 2 2v7h-4v5H5v-5H1v-7a2 2 0 0 1 2-2zm4 8v4h10v-4z"/></svg>907 215 4490</li>
        <li><svg viewBox="0 0 24 24"><path d="M2 5h20v14H2zm2 2v.5l8 5 8-5V7z"/></svg>hello@brightwayhaus.ca</li>
      </ul>
    </div>
  </section>

  <section class="card card--back" aria-label="Card back">
    <div class="brand"><span class="brand__square"></span>Brightway Haus Inc.</div>
    <p class="tagline">
      <span class="tagline__rule tagline__rule--left"></span>
      Where <span class="tagline__accent">Shine</span> Counts
      <span class="tagline__rule tagline__rule--right"></span>
    </p>
  </section>
</body>
</html>
```